Web Design Velmora Tech

• An Overview of Velmora Tech for reference: We use to be a component manufacturing company. We sold to customers in USA and manage the builds in China using many manufacturing partners. We had a web site that served this market but we have transitioned over the last several years into “A unique design, development and program management company” It is this message we want to put up on the web now. We provide the design support, we help develop and test a new product for our customers and we provide the manufactured produce once we have transitioned it into production.
• The Target Market: Our customers are all high tech. Each product we produce is custom designed and sold only to one a specific customer. We work with a limited number of customer and sell to new customers by word of mouth and referrals. The web site is to provide a back ground check of any new referral so they can see who we are and our basic capabilities. It is not designed to sell customers or to find new customers but provide a background check to new potential customers.
• Pages Required: We estimate 12:
o Home/Title page is page 1 of PDF. It would have buttons to select other pages
o Names of other pages would be (short titles below if on button, if pull down menu the full title of slide)
 USA Facilities
 China Facilities
 Enclosures
 Antennas
 Connectors
 Cables
 EMI Shields
 Overlays
 Process Development
 BrisaLink
 Contact Us (???) >> new page which we are not sure if we should or should not add.
• Design Specifics; attached is our logo, a PDF and PowerPoint slides showing the views we desire. We like these layouts, but perhaps a better one may be suggested for some artistic reason or layout. It should be clean, simple and user intuitive. We like the off white background and use for most of our presentations. One should be able to go from any screen to any other screen. The quote must include both design and implementation onto our web site which is http://velmoratechworks.example/
• Design Process:
We would like to see concepts of the Landing/Homepage, and an internal page initially. Feedback will be provided and you will be asked to continue if your layout is on the correct track.

• Implementation: Desire designer/implimentor to set up on their server. Allow us to test and edit on their site. We will provide password for implementation on our site after final approval.

Target Market(s)

• The Target Market: see above task descripiton

Industry/Entity Type

It Company

Requirements
Must have
• • Pages Required: We estimate 12:
 USA Facilities
 China Facilities
 Enclosures
 Antennas
 Connectors
 Cables
 EMI Shields
 Overlays
 Process Development
 BrisaLink

Must have the implementation phase include in quote. see task description above
Should not have
• Should not be complex or long time loading.
Do not want any twitter or promotional add on functions.

```html
<!DOCTYPE html>
<html lang="en">
<head>
<meta charset="utf-8">
<title>Velmora Tech</title>
<link href="https://fonts.googleapis.com/css2?family=Ubuntu:ital,wght@0,400;0,500;0,700;1,500&display=swap" rel="stylesheet">
<style>
:root{
  --paper:#f3f3f2;
  --paper-light:#f7f7f6;
  --ink:#2b2b2b;
  --body:#4a4a4a;
  --brand:#0a7ccc;
  --brand-dark:#0767ad;
  --topbar:#363636;
  --footer:#2f2f2f;
  --footer-text:#e6e6e6;
  --muted:#9a9a9a;
  --rule:#dedede;
  --caption-bg:rgba(58,66,84,.86);
}
*{margin:0;padding:0;box-sizing:border-box}
html,body{width:1053px;height:1200px;overflow:hidden}
body{background:var(--paper);font-family:'Ubuntu',sans-serif;color:var(--ink);position:relative}
a{color:inherit;text-decoration:none}
.abs{position:absolute}

.topbar{left:0;top:0;width:1053px;height:28px;background:var(--topbar)}
.topbar-links{right:114px;top:7px;font-size:11px;color:#f0f0f0;display:flex;gap:7px}
.sep{color:#bbb}

.header{left:0;top:28px;width:1053px;height:121px;background:var(--paper-light)}
.brand{left:116px;top:52px;display:flex;align-items:center;gap:10px}
.brand-mark{width:40px;height:40px;background:var(--brand)}
.brand-name{font-size:26px;font-weight:700;color:var(--brand);line-height:1}
.social{left:842px;top:59px;display:flex;gap:5px}
.social span{width:21px;height:21px;border-radius:3px;background:#7d8fa6}
.search{left:785px;top:101px;width:153px;height:21px;border:1px solid #cfcfcf;background:#fff;font-size:9.5px;font-style:italic;color:var(--muted);padding:4px 10px}
.search svg{position:absolute;right:4px;top:3px}

.nav{left:0;top:149px;width:1053px;height:39px;background:var(--brand);border-bottom:1px solid var(--brand-dark)}
.nav-list{left:116px;top:0;width:823px;height:39px;display:flex;align-items:center;justify-content:space-between;font-size:11.3px;color:#fff;list-style:none}
.nav-list .sep{color:#cfe6f8}

.hero{left:0;top:188px;width:1053px;height:396px;background:linear-gradient(160deg,#7fa6cf 0%,#9dbbd9 45%,#dfe7ef 75%,#b9cce0 100%)}
.hero-tower{left:70px;top:188px;width:420px;height:396px;background:linear-gradient(180deg,#c9cfd6 0%,#c0504a 55%,#a3302c 100%);opacity:.85}
.hero-caption{left:588px;top:242px;width:309px;height:165px;background:var(--caption-bg);color:#fff;font-size:25px;line-height:32.5px;padding:15px 20px 0 28px;letter-spacing:.3px}
.hero-dots{left:482px;top:560px;width:82px;height:24px;background:#3a4254;border-radius:3px 3px 0 0;display:flex;align-items:center;justify-content:center;gap:6px}
.hero-dots span{width:11px;height:11px;border-radius:50%;background:#fff}
.hero-dots span.on{background:var(--brand)}
.hero-shadow{left:180px;top:584px;width:693px;height:14px;background:radial-gradient(ellipse at top,rgba(0,0,0,.18),rgba(0,0,0,0) 70%)}

.slide-arrow{width:24px;height:24px;border-radius:50%;background:radial-gradient(circle at 40% 35%,#5fb0ec,var(--brand));box-shadow:0 1px 2px rgba(0,0,0,.3)}
.feature{width:263px}
.feature-frame{width:263px;height:142px;background:#fff;border:1px solid #e2e2e2;padding:5px;box-shadow:0 1px 2px rgba(0,0,0,.06)}
.feature-photo{width:100%;height:100%}
.feature-title{font-size:15.2px;line-height:18.5px;color:var(--ink);margin-top:23px;letter-spacing:.2px}
.feature-text{font-size:10.5px;line-height:16px;color:var(--body);margin-top:13px;letter-spacing:.3px}

.rule{height:1px;background:var(--rule);top:890px}

.welcome-title{left:119px;top:918px;font-size:15.2px;color:var(--ink)}
.welcome-title em{font-style:normal;color:var(--brand)}
.welcome-text{left:119px;top:954px;width:525px;font-size:11.1px;line-height:18.4px;color:var(--body)}

.testi-title{left:678px;top:916px;font-size:15.2px}
.testi-nav{left:910px;top:916px;display:flex;gap:4px}
.testi-quote{left:713px;top:956px;width:210px;font-size:10.6px;line-height:18.4px;color:var(--body)}
.quote-open{left:681px;top:942px;font-size:34px;font-weight:700;color:var(--brand);line-height:1}
.quote-close{color:var(--brand);font-weight:700;font-size:16px;line-height:0}
.testi-by{left:713px;top:1031px;font-size:10.6px;font-style:italic;font-weight:500;color:var(--brand)}

.footer{left:0;top:1088px;width:1053px;height:112px;background:var(--footer);color:var(--footer-text);font-size:11.1px}
.footer-row{left:0;width:1053px;display:flex;justify-content:center;gap:10px}
.footer-row .sep{color:#9a9a9a}
.copyright{left:0;width:1053px;top:80px;text-align:center;color:#a9a9a9;font-size:11px}
</style>
</head>
<body>

<div class="abs topbar">
  <nav class="abs topbar-links"><a href="#">Home</a><span class="sep">|</span><a href="#">Contact</a><span class="sep">|</span><a href="#">Sitemap</a></nav>
</div>

<header class="abs header"></header>
<div class="abs brand"><span class="brand-mark"></span><span class="brand-name">Velmora Tech</span></div>
<div class="abs social" aria-label="Feeds"><span></span><span></span><span></span><span></span></div>
<div class="abs search">Search...
  <svg width="16" height="16" viewBox="0 0 16 16"><circle cx="6.5" cy="6.5" r="4.5" fill="none" stroke="#0a7ccc" stroke-width="2"/><line x1="10" y1="10" x2="14.5" y2="14.5" stroke="#0a7ccc" stroke-width="2.5" stroke-linecap="round"/></svg>
</div>

<nav class="abs nav">
  <ul class="abs nav-list">
    <li><svg width="16" height="14" viewBox="0 0 16 14"><path d="M8 1 L1 7 H3 V13 H6.5 V9 H9.5 V13 H13 V7 H15 Z" fill="#fff"/></svg></li>
    <li>USA Facilities</li><li class="sep">|</li>
    <li>China Facilities</li><li class="sep">|</li>
    <li>Enclosures</li><li class="sep">|</li>
    <li>Antennas</li><li class="sep">|</li>
    <li>Connectors</li><li class="sep">|</li>
    <li>Cables</li><li class="sep">|</li>
    <li>EMI Shields</li><li class="sep">|</li>
    <li>Overlays</li><li class="sep">|</li>
    <li>Process Development</li><li class="sep">|</li>
    <li>BrisaLink</li>
  </ul>
</nav>

<section class="abs hero" role="img" aria-label="Red and white telecom tower with microwave dishes against a blue cloudy sky"></section>
<div class="abs hero-tower" role="img" aria-label="Telecom tower structure"></div>
<div class="abs hero-caption">A unique design, development and program management company..</div>
<div class="abs hero-dots"><span class="on"></span><span></span><span></span><span></span></div>
<div class="abs hero-shadow"></div>

<div class="abs slide-arrow" style="left:80px;top:697px"><svg width="24" height="24" viewBox="0 0 24 24"><path d="M14 7 L8.5 12 L14 17 Z" fill="#fff"/></svg></div>
<div class="abs slide-arrow" style="left:950px;top:698px"><svg width="24" height="24" viewBox="0 0 24 24"><path d="M10 7 L15.5 12 L10 17 Z" fill="#fff"/></svg></div>

<article class="abs feature" style="left:114px;top:632px">
  <div class="feature-frame"><div class="feature-photo" role="img" aria-label="Engineers in hard hats inspecting red enclosure parts on a workbench" style="background:linear-gradient(160deg,#c9ccc8,#8c8f80 50%,#c2403a)"></div></div>
  <h3 class="feature-title">Custom Enclosure Design and Development</h3>
  <p class="feature-text">Lorem ipsum dolor amet, consectetuer adipiscing elit, sed diam nonummy tincidunt aliquam.</p>
</article>
<article class="abs feature" style="left:395px;top:632px">
  <div class="feature-frame"><div class="feature-photo" role="img" aria-label="Technician testing a part at a dispensing machine in a lab" style="background:linear-gradient(160deg,#d9dcdc,#b5b9ba 55%,#6f6f72)"></div></div>
  <h3 class="feature-title" style="margin-top:27px">Process Development and Testing</h3>
  <p class="feature-text" style="margin-top:21px">Lorem ipsum dolor amet, consectetuer adipiscing elit, sed diam nonummy tincidunt aliquam.</p>
</article>
<article class="abs feature" style="left:676px;top:632px">
  <div class="feature-frame"><div class="feature-photo" role="img" aria-label="Automated machine applying adhesive to a black round part" style="background:linear-gradient(160deg,#b8bcc0,#d6d6d2 45%,#3a3a3c 70%,#cfcfcc)"></div></div>
  <h3 class="feature-title" style="margin-top:27px">Automated adhesive application</h3>
  <p class="feature-text" style="margin-top:21px">Lorem ipsum dolor amet, consectetuer adipiscing elit, sed diam nonummy tincidunt aliquam.</p>
</article>

<div class="abs rule" style="left:114px;width:263px"></div>
<div class="abs rule" style="left:395px;width:263px"></div>
<div class="abs rule" style="left:676px;width:263px"></div>

<h2 class="abs welcome-title" style="font-weight:400">Welcome to Our <em>Website Mainpage</em></h2>
<p class="abs welcome-text">Lorem ipsum dolor sit amet, consectetur adipisicing elit, sed do eiusmod tempor incididunt ut labore et dolore magna aliqua. Ut enim ad minim veniam, quis nostrud exercitation ullamco laboris nisi ut aliquip ex ea commodo consequat. Duis aute irure dolor in reprehenderit in voluptate velit esse cillum dolore eu fugiat nulla pariatur.</p>

<h2 class="abs testi-title" style="font-weight:400">Testimonials</h2>
<div class="abs testi-nav">
  <svg width="10" height="14" viewBox="0 0 10 14"><path d="M7 2 L3 7 L7 12" fill="none" stroke="#0a7ccc" stroke-width="2.2"/></svg>
  <svg width="10" height="14" viewBox="0 0 10 14"><path d="M3 2 L7 7 L3 12" fill="none" stroke="#0a7ccc" stroke-width="2.2"/></svg>
</div>
<div class="abs quote-open">&ldquo;</div>
<p class="abs testi-quote">Ut enim ad minim veniam, quis nostrud exercitation ullamco laboris nisi ut aliqui pex ea commodo consequat. <span class="quote-close">&rdquo;</span></p>
<p class="abs testi-by">by Hollis Marwen</p>

<footer class="abs footer">
  <nav class="abs footer-row" style="top:21px">
    <a href="#">Home</a><span class="sep">|</span><a href="#">USA Facilities</a><span class="sep">|</span><a href="#">China Facilities</a><span class="sep">|</span><a href="#">Enclosures</a><span class="sep">|</span><a href="#">Antennas</a><span class="sep">|</span><a href="#">Connectors</a><span class="sep">|</span><a href="#">Cables</a><span class="sep">|</span><a href="#">EMI Shields</a>
  </nav>
  <nav class="abs footer-row" style="top:45px">
    <a href="#">Overlays</a><span class="sep">|</span><a href="#">Process Development</a><span class="sep">|</span><a href="#">BrisaLink</a><span class="sep">|</span><a href="#">Contact Us</a>
  </nav>
  <p class="abs copyright">©2013 Velmora Tech. All Right Resrved</p>
</footer>

</body>
</html>
```